Business Card Design Project

We need a business card for a new technology services company. We develop software and implement software packages for our business customers and although we will begin with just one or two service offerings, our service offerings will expand over time. Our name comes from the an author, KL Barrow, and his "idea" was that opportunity should be based on ability and achievement, not on social status.

We would like to see a design that is standard in its size and shape, but stands apart in its dramatic color contrasts. The card should not use too many colors - the colors used in the background should highlight the brilliant blues of the logo (see attachment) to dramatic effect. The background should not be white.

If necessary, you can change the color of the words "KL Barrow", but not the word "Idea".

Card size should be U.S. standard 2 inches by 3.5 inches and provide for 1/8 inch bleed area on each side.

We need a design for both sides of the business card, one side communicating the company logo and contact information, the other side being purely graphical, incorporating the logo but no other information.

Contact Information Required:
Kate Brook
KateBrook@klbarrowvista.com
614-387-2259

Target Market(s)

Business executives

Industry/Entity Type

Software

Requirements
Must have
• It must have the full company logo on one side, and at least the graphic element of the logo on the other. Either that or the full logo on both.
Nice to have
• It would be nice to have a design that could work without needing two different textures. For example, it would be nice if the entire card could be shiny, not just parts of the card.

It would also be nice if texture is something we could add later.
Should not have
• The card should not use the color green.

```html
<!DOCTYPE html>
<html lang="en">
<head>
<meta charset="utf-8">
<title>KL Barrow Vista — Business Card</title>
<link rel="stylesheet" href="https://fonts.googleapis.com/css2?family=Source+Sans+3:wght@400;600&display=swap">
<style>
  :root {
    --ink: #000000;
    --paper: #ffffff;
    --brilliant-blue: #06cde0;
    --steel-grey: #a4a6a9;
    --edge: #3a3a3a;
    --text-font: "Source Sans 3", "Myriad Pro", Arial, sans-serif;
  }
  * { box-sizing: border-box; margin: 0; padding: 0; }
  html, body {
    width: 1200px;
    height: 320px;
    overflow: hidden;
    background: var(--paper);
  }
  .sheet {
    position: relative;
    width: 1200px;
    height: 320px;
    font-family: var(--text-font);
  }
  .card {
    position: absolute;
    top: 0;
    width: 559px;
    height: 320px;
    background: var(--ink);
    overflow: hidden;
  }
  .card--graphic { left: 0; }
  .card--contact {
    left: 641px;
    border: 1px solid var(--edge);
  }
  .diagonal-band {
    position: absolute;
    inset: 0;
    width: 100%;
    height: 100%;
  }
  .brand-mark {
    position: absolute;
    border-radius: 50%;
    background: var(--brilliant-blue);
  }
  .brand-name {
    position: absolute;
    color: var(--steel-grey);
    font-weight: 400;
    white-space: nowrap;
    line-height: 1;
  }
  .card--graphic .brand-mark {
    left: 404px;
    top: 128px;
    width: 84px;
    height: 84px;
  }
  .card--graphic .brand-name {
    left: 74px;
    top: 218px;
    font-size: 46px;
    letter-spacing: -0.5px;
  }
  .card--contact .brand-mark {
    left: 470px;
    top: 36px;
    width: 46px;
    height: 46px;
  }
  .card--contact .brand-name {
    right: 108px;
    top: 90px;
    font-size: 30px;
    letter-spacing: -0.3px;
  }
  .contact {
    position: absolute;
    left: 36px;
    top: 166px;
    color: var(--ink);
  }
  .contact__name {
    font-size: 33px;
    font-weight: 400;
    line-height: 1;
    margin-bottom: 30px;
  }
  .contact__line {
    font-size: 22.5px;
    line-height: 32px;
  }
</style>
</head>
<body>
<main class="sheet">
  <section class="card card--graphic" aria-label="Card front">
    <span class="brand-mark" aria-hidden="true"></span>
    <span class="brand-name">KL Barrow Vista</span>
  </section>

  <section class="card card--contact" aria-label="Card back">
    <svg class="diagonal-band" viewBox="0 0 559 320" preserveAspectRatio="none" aria-hidden="true">
      <polygon points="0,0 559,320 0,320" fill="var(--brilliant-blue)"/>
    </svg>
    <span class="brand-mark" aria-hidden="true"></span>
    <span class="brand-name">KL Barrow Vista</span>
    <div class="contact">
      <p class="contact__name">Kate Brook</p>
      <p class="contact__line">KateBrook@klbarrowvista.com</p>
      <p class="contact__line">614-387-2259</p>
    </div>
  </section>
</main>
</body>
</html>
```